Plakat für Hausverwaltung
Zielgruppe
Hausverwaltung
(Verwaltung von Wohn- und Gewerbeimmobilien)
Aufgabenstellung
Es soll ein Werbeplakat werden, Die Inhalte der Dienstleistung und die Firmenfarben kann der Webseite entnommen werden.
Ein guter Werbespruch und ansprechendes Desing ohne viel Schrift.

```html
<!DOCTYPE html>
<html lang="de">
<head>
<meta charset="utf-8">
<title>KWR Hausverwaltung – Plakat</title>
<link rel="stylesheet" href="https://fonts.googleapis.com/css2?family=Poppins:wght@400;600;700&family=Source+Serif+4:opsz,wght@8..60,700;8..60,800&family=Libre+Baskerville&display=swap">
<style>
  :root{
    --page:#9e9e9e;
    --white:#ffffff;
    --stone:#cdc8c3;
    --taupe:#8c8377;
    --taupe-light:#b5aea5;
    --ink:#0b0b0b;
    --text-dark:#222222;
    --footer-top:#2a2a2a;
    --footer-bottom:#474747;
    --icon:#9a9289;
  }
  *{margin:0;padding:0;box-sizing:border-box}
  html,body{width:923px;height:1200px;overflow:hidden;background:var(--page)}
  .poster{position:absolute;left:31px;top:300px;width:860px;height:600px;overflow:hidden;background:var(--ink);font-family:'Poppins',sans-serif}
  .poster-shapes{position:absolute;inset:0}
  .brand{position:absolute;left:40px;top:0;width:320px;height:124px;text-align:center}
  .brand-mark{position:absolute;left:0;right:0;top:34px;font-family:'Libre Baskerville',serif;font-size:27px;letter-spacing:10px;color:var(--text-dark)}
  .brand-name{position:absolute;left:0;right:0;top:75px;font-family:'Libre Baskerville',serif;font-size:12.5px;color:var(--text-dark);white-space:nowrap}
  .headline{position:absolute;left:53px;top:146px;font-family:'Source Serif 4',serif;font-weight:800;font-size:43px;line-height:42px;color:var(--text-dark);letter-spacing:-0.5px}
  .subline{position:absolute;left:54px;top:238px;font-family:'Source Serif 4',serif;font-weight:700;font-size:16.5px;color:var(--text-dark)}
  .offers-title{position:absolute;left:54px;top:287px;font-weight:700;font-size:25px;color:var(--white)}
  .offer{position:absolute;top:352px;width:231px;height:164px;border:2.5px solid var(--white);border-radius:14px;padding:20px 8px 0 33px;color:var(--white)}
  .offer h3{font-weight:700;font-size:11.5px;letter-spacing:.2px;color:var(--stone);margin-left:-18px;margin-bottom:5px;white-space:nowrap}
  .offer p{font-size:10.6px;line-height:12px}
  .offer-1{left:74px}
  .offer-2{left:327px;padding-left:22px}
  .offer-2 h3{margin-left:-7px}
  .offer-3{left:579px;padding-left:22px}
  .offer-3 h3{margin-left:0;text-align:center}
  .offer-badge{position:absolute;top:408px;width:44px;height:44px;border-radius:50%;background:radial-gradient(circle at 40% 35%,#f1eeea,#c8c2bb);border:2.5px solid var(--ink);box-shadow:0 0 0 2px var(--white);font-family:'Source Serif 4',serif;font-weight:800;font-size:28px;line-height:38px;text-align:center;color:var(--ink)}
  .contact{position:absolute;left:0;right:0;top:538px;height:62px;background:linear-gradient(var(--footer-top),var(--footer-bottom));display:flex;justify-content:center;align-items:center;gap:14px;color:var(--white);font-weight:700;font-size:16px}
  .contact-item{display:flex;align-items:center;gap:6px}
  .contact-icon{width:15px;height:15px}
  .contact-sep{width:2px;height:24px;background:var(--white)}
</style>
</head>
<body>
<main class="poster">
  <svg class="poster-shapes" width="860" height="600" viewBox="0 0 860 600">
    <defs>
      <linearGradient id="ringTaupe" x1="0" y1="0" x2="1" y2="1">
        <stop offset="0" stop-color="#6f675d"/>
        <stop offset=".5" stop-color="#c9c2b8"/>
        <stop offset="1" stop-color="#7d756b"/>
      </linearGradient>
      <linearGradient id="photoTone" x1="0" y1="0" x2="0" y2="1">
        <stop offset="0" stop-color="#c9c6bd"/>
        <stop offset=".45" stop-color="#6d7a86"/>
        <stop offset="1" stop-color="#2c3444"/>
      </linearGradient>
    </defs>
    <rect class="brand-panel" x="0" y="0" width="860" height="124" fill="var(--white)"/>
    <polygon class="headline-panel" points="0,124 860,124 860,282 0,282" fill="var(--stone)"/>
    <polygon class="offers-bar" points="0,282 380,282 410,328 0,328" fill="var(--taupe)"/>
    <polygon class="offers-stripe" points="354,282 378,282 410,328 386,328" fill="var(--taupe-light)"/>
    <polygon class="offers-stripe" points="385,282 405,282 438,328 418,328" fill="var(--white)"/>
    <rect class="offers-field" x="0" y="328" width="860" height="210" fill="var(--ink)"/>
    <polygon points="410,282 860,282 860,328 440,328" fill="var(--ink)"/>
    <circle class="ring-outer" cx="660" cy="2" r="338" fill="url(#ringTaupe)"/>
    <circle class="ring-inner" cx="660" cy="2" r="305" fill="var(--ink)"/>
    <circle class="ring-line" cx="660" cy="2" r="288" fill="var(--white)"/>
    <circle cx="660" cy="2" r="282" fill="url(#photoTone)" role="img" aria-label="Teamfoto: drei Mitarbeitende in Businesskleidung vor einem Regal mit Aktenordnern"/>
  </svg>

  <header class="brand">
    <div class="brand-mark">KWR</div>
    <div class="brand-name">Haus- und Grundstücksverwaltungs GmbH</div>
  </header>

  <h1 class="headline">Ihre Immobilie<br>in guten Händen</h1>
  <p class="subline">KWR Haus- und Immobilienverwaltungs GmbH</p>

  <h2 class="offers-title">Unsere Angebote</h2>

  <section class="offer offer-1">
    <h3>SONDEREIGENTUMVERWALTUNG</h3>
    <p>Unter Sondereigentumsverwaltung versteht man die Verwaltung der einzelnen Eigentumswohnung.<br>Die Verwaltung des<br>Sondereigentums bieten wir Ihnen gerne zu einem günstigen Monats- / Jahrespreis an</p>
  </section>
  <section class="offer offer-2">
    <h3>WOHNEIGENTUMSVERWALTUNG</h3>
    <p>Zu den Grundleistungen die wir<br>für Sie übernehmen gehören vor allem die unabdingbaren, in<br>den § 27 Absatz 1 und 2 WEG aufgeführten gesetzlichen Aufgaben. Die Grundleistungen der ordnungsgemäßen Verwaltung sichern der Eigentümergemeinschaft eine sachgerechte Verwaltung.</p>
  </section>
  <section class="offer offer-3">
    <h3>MIETVERWALTUNG</h3>
    <p>Wie viel Arbeit Sie uns überlassen, liegt ganz bei Ihnen. Einige unserer Kundenkümmern sich zum Beispiel gerne selbst um die Auswahl der Mieter andere wiederum möchten sich nur nicht mit der Betriebskostenabrechnung belasten.</p>
  </section>

  <div class="offer-badge" style="left:53px">1</div>
  <div class="offer-badge" style="left:295px">2</div>
  <div class="offer-badge" style="left:547px">3</div>

  <footer class="contact">
    <span class="contact-item">
      <svg class="contact-icon" viewBox="0 0 16 16"><circle cx="8" cy="8" r="8" fill="var(--icon)"/><path d="M5 4.2l1.6-.4 1 2.1-1 .8a6 6 0 0 0 2.7 2.7l.8-1 2.1 1-.4 1.6c-3.8.3-7.1-3-6.8-6.8z" fill="var(--footer-top)"/></svg>
      06421 530219
    </span>
    <span class="contact-sep"></span>
    <span class="contact-item">
      <svg class="contact-icon" viewBox="0 0 16 16"><circle cx="8" cy="8" r="8" fill="var(--icon)"/><rect x="4" y="5" width="8" height="6" fill="none" stroke="var(--footer-top)" stroke-width="1"/><path d="M4 5l4 3.2L12 5" fill="none" stroke="var(--footer-top)" stroke-width="1"/></svg>
      info@kwr-lahnau.de
    </span>
    <span class="contact-sep"></span>
    <span class="contact-item">
      <svg class="contact-icon" viewBox="0 0 16 16"><circle cx="8" cy="8" r="8" fill="var(--icon)"/><g fill="none" stroke="var(--footer-top)" stroke-width=".9"><circle cx="8" cy="8" r="4.2"/><ellipse cx="8" cy="8" rx="1.8" ry="4.2"/><path d="M3.8 8h8.4"/></g></svg>
      www.kwr-lahnau.de
    </span>
  </footer>
</main>
</body>
</html>
```